Web Design for company in the healthcare industry

We need a web design for a new company in the healthcare industry (telehealth) which allows patients to schedule appointments at their convenience, view and monitor their results, and consult with specialists that fit their requirements. The aim is to help patients take charge of their own health.

We already have a logo (attached) and are working with a developer who will do all the back end programming once the design is ready. Apart from the colours in the logo, we think shades of gray would work well.

Target Market(s)

I imagine the vast majority would be professionals from 30-50 years old.

Industry/Entity Type

Health And Wellness

Number of Pages Required

4 page

Requirements
Must have
• Hand-sketched graphics, particularly on landing page.
Should not have
• We don't want any photographs of people

```html
<!DOCTYPE html>
<html lang="en">
<head>
<meta charset="utf-8">
<title>Medora – Specialists</title>
<link href="https://fonts.googleapis.com/css2?family=Open+Sans:wght@400;600;700&display=swap" rel="stylesheet">
<style>
:root{
  --blue:#1e8bd0;
  --navy:#0f2a44;
  --navy-dark:#0b2036;
  --green:#7cc242;
  --ink:#2d3338;
  --grey:#7a8087;
  --line:#e3e6e9;
  --soft:#f3f4f5;
  --white:#ffffff;
}
*{margin:0;padding:0;box-sizing:border-box}
html,body{width:789px;height:1200px;overflow:hidden;background:var(--white)}
body{font-family:"Open Sans",Arial,sans-serif;color:var(--ink);position:relative}
.site-header{height:56px;display:flex;align-items:center;justify-content:space-between;padding:0 66px}
.brand{display:flex;align-items:center;gap:7px;font-size:24px;font-weight:700;color:var(--blue)}
.brand-dot{width:12px;height:12px;border-radius:50%;background:var(--blue)}
.main-nav{display:flex;gap:20px;font-size:11px;color:var(--blue)}
.main-nav a{text-decoration:none;color:inherit;position:relative}
.main-nav .active{color:var(--green)}
.main-nav .active svg{position:absolute;left:0;top:16px}
.breadcrumb{margin-top:44px;height:19px;background:var(--soft);padding:0 66px;font-size:9px;color:var(--grey);line-height:19px}
.page-title{text-align:center;margin-top:24px}
.page-title h1{font-size:20px;font-weight:600;letter-spacing:2px;color:var(--blue);display:inline-flex;align-items:center;gap:8px}
.page-title svg.pulse{display:block;margin:6px auto 0}
.specialist-group{padding:0 66px}
.group-heading{font-size:16px;font-weight:700;color:var(--ink);padding-bottom:8px;border-bottom:1px solid var(--line);margin-bottom:12px}
.cardio{margin-top:28px}
.neuro{margin-top:54px}
.card-row{display:flex;gap:10px}
.specialist-card{width:157px;border:1px solid var(--line);background:var(--white)}
.portrait{height:112px;background:radial-gradient(circle at 50% 48%,#dfe3e6 0 34%,#f1f2f3 35%)}
.card-body{padding:8px 8px 6px}
.card-body h3{font-size:11px;font-weight:700}
.role{font-size:8px;color:var(--grey);margin-bottom:5px}
.bio{font-size:7.5px;line-height:1.45;color:var(--grey);margin-bottom:6px}
.contact-line{display:flex;align-items:center;gap:4px;font-size:7px;color:var(--grey);margin-bottom:3px}
.socials{display:flex;gap:5px;border-top:1px solid var(--line);padding:6px 8px}
.socials span{width:9px;height:9px;border-radius:50%;background:#c7ccd1}
.site-footer{position:absolute;left:0;top:968px;width:789px;height:232px;background:var(--navy);color:#c9d4df}
.footer-cols{display:flex;padding:20px 66px 0;gap:22px;height:150px}
.footer-cols h4{font-size:10px;font-weight:700;color:var(--white);margin-bottom:9px;letter-spacing:.5px}
.quick-links{width:120px}
.quick-links li{list-style:none;font-size:8px;margin-bottom:5px;display:flex;gap:5px;align-items:center}
.quick-links li::before{content:"";width:3px;height:3px;border-radius:50%;background:var(--green)}
.map{width:108px;height:88px;margin-top:18px;background:linear-gradient(135deg,#d7e3d0,#cfd9e4)}
.touch{width:140px;font-size:7.5px;line-height:1.5}
.touch p{margin-bottom:6px}
.touch .row{display:flex;gap:5px;align-items:center;margin-bottom:4px}
.contact-form{width:160px}
.form-grid{display:flex;gap:5px}
.form-fields{display:flex;flex-direction:column;gap:4px;width:70px}
.field{height:14px;background:var(--white);font-size:7px;color:#9aa3ab;padding:0 4px;line-height:14px}
.message{width:85px;height:50px;background:var(--white);font-size:7px;color:#9aa3ab;padding:3px 4px}
.submit{margin:8px 0 0 75px;width:40px;height:13px;background:var(--green);color:var(--white);font-size:7px;text-align:center;line-height:13px}
.footer-bar{height:82px;border-top:1px solid #1f3c58;background:var(--navy-dark);display:flex;justify-content:space-between;align-items:center;padding:0 66px 20px;font-size:8px}
.footer-social{display:flex;gap:7px}
.footer-social span{width:9px;height:9px;border-radius:50%;background:#9fb0c1}
.to-top{position:absolute;right:14px;top:104px;width:18px;height:14px;background:var(--white);color:var(--navy);font-size:7px;text-align:center;line-height:14px}
</style>
</head>
<body>
<header class="site-header">
  <div class="brand"><span class="brand-dot"></span>Medora</div>
  <nav class="main-nav">
    <a href="#">Home</a>
    <a href="#">Health Packages</a>
    <a href="#">Appointments</a>
    <a href="#" class="active">Specialists<svg width="56" height="5" viewBox="0 0 56 5"><path d="M0 3 Q14 0 28 3 T56 2" stroke="#7cc242" stroke-width="1.5" fill="none"/></svg></a>
    <a href="#">Contact Us</a>
  </nav>
</header>

<div class="breadcrumb">Home &gt; Specialists</div>

<div class="page-title">
  <h1><svg width="16" height="16" viewBox="0 0 16 16"><circle cx="8" cy="5" r="3.5" fill="#1e8bd0"/><path d="M1 16c0-4 3-6 7-6s7 2 7 6z" fill="#1e8bd0"/><path d="M11 11v3M9.5 12.5h3" stroke="#fff" stroke-width="1.2"/></svg>SPECIALISTS</h1>
  <svg class="pulse" width="40" height="10" viewBox="0 0 40 10"><polyline points="0,6 14,6 17,1 20,9 23,4 26,6 40,6" fill="none" stroke="#7cc242" stroke-width="1.3"/></svg>
</div>

<section class="specialist-group cardio">
  <h2 class="group-heading">Cardio Specialists</h2>
  <div class="card-row">
    <article class="specialist-card">
      <div class="portrait" role="img" aria-label="Portrait of cardiologist Aaron Pell"></div>
      <div class="card-body"><h3>Aaron Pell</h3><p class="role">Senior cardio Specialist</p>
        <p class="bio">Caring for adult hearts with clear plans, steady follow up and calm advice.</p>
        <p class="contact-line"><svg width="7" height="7" viewBox="0 0 10 10"><path d="M2 1l2 2-1 1.5q1.5 2.5 3.5 3.5L8 7l2 2-1.5 1Q3 9 1 2.5z" fill="#1e8bd0"/></svg>1-800-555-0142 · Extension 114</p>
        <p class="contact-line"><svg width="7" height="7" viewBox="0 0 10 10"><path d="M2 1l2 2-1 1.5q1.5 2.5 3.5 3.5L8 7l2 2-1.5 1Q3 9 1 2.5z" fill="#1e8bd0"/></svg>1-800-555-0177</p>
        <p class="contact-line"><svg width="7" height="6" viewBox="0 0 10 8"><rect x=".5" y=".5" width="9" height="7" fill="none" stroke="#1e8bd0"/><path d="M.5 .5L5 4.5 9.5.5" fill="none" stroke="#1e8bd0"/></svg>a.pell@medora.com</p>
      </div>
      <div class="socials"><span></span><span></span><span></span><span></span><span></span></div>
    </article>
    <article class="specialist-card">
      <div class="portrait" role="img" aria-label="Portrait of cardiologist Ravi Mehta"></div>
      <div class="card-body"><h3>Ravi Mehta</h3><p class="role">Senior cardio Specialist</p>
        <p class="bio">Caring for adult hearts with clear plans, steady follow up and calm advice.</p>
        <p class="contact-line"><svg width="7" height="7" viewBox="0 0 10 10"><path d="M2 1l2 2-1 1.5q1.5 2.5 3.5 3.5L8 7l2 2-1.5 1Q3 9 1 2.5z" fill="#1e8bd0"/></svg>1-800-555-0143 · Extension 115</p>
        <p class="contact-line"><svg width="7" height="7" viewBox="0 0 10 10"><path d="M2 1l2 2-1 1.5q1.5 2.5 3.5 3.5L8 7l2 2-1.5 1Q3 9 1 2.5z" fill="#1e8bd0"/></svg>1-800-555-0178</p>
        <p class="contact-line"><svg width="7" height="6" viewBox="0 0 10 8"><rect x=".5" y=".5" width="9" height="7" fill="none" stroke="#1e8bd0"/><path d="M.5 .5L5 4.5 9.5.5" fill="none" stroke="#1e8bd0"/></svg>r.mehta@medora.com</p>
      </div>
      <div class="socials"><span></span><span></span><span></span><span></span><span></span></div>
    </article>
    <article class="specialist-card">
      <div class="portrait" role="img" aria-label="Portrait of cardiologist Owen Carr"></div>
      <div class="card-body"><h3>Owen Carr</h3><p class="role">Senior cardio Specialist</p>
        <p class="bio">Caring for adult hearts with clear plans, steady follow up and calm advice.</p>
        <p class="contact-line"><svg width="7" height="7" viewBox="0 0 10 10"><path d="M2 1l2 2-1 1.5q1.5 2.5 3.5 3.5L8 7l2 2-1.5 1Q3 9 1 2.5z" fill="#1e8bd0"/></svg>1-800-555-0144 · Extension 116</p>
        <p class="contact-line"><svg width="7" height="7" viewBox="0 0 10 10"><path d="M2 1l2 2-1 1.5q1.5 2.5 3.5 3.5L8 7l2 2-1.5 1Q3 9 1 2.5z" fill="#1e8bd0"/></svg>1-800-555-0179</p>
        <p class="contact-line"><svg width="7" height="6" viewBox="0 0 10 8"><rect x=".5" y=".5" width="9" height="7" fill="none" stroke="#1e8bd0"/><path d="M.5 .5L5 4.5 9.5.5" fill="none" stroke="#1e8bd0"/></svg>o.carr@medora.com</p>
      </div>
      <div class="socials"><span></span><span></span><span></span><span></span><span></span></div>
    </article>
    <article class="specialist-card">
      <div class="portrait" role="img" aria-label="Portrait of cardiologist Daniel Ruiz"></div>
      <div class="card-body"><h3>Daniel Ruiz</h3><p class="role">Senior cardio Specialist</p>
        <p class="bio">Caring for adult hearts with clear plans, steady follow up and calm advice.</p>
        <p class="contact-line"><svg width="7" height="7" viewBox="0 0 10 10"><path d="M2 1l2 2-1 1.5q1.5 2.5 3.5 3.5L8 7l2 2-1.5 1Q3 9 1 2.5z" fill="#1e8bd0"/></svg>1-800-555-0145 · Extension 117</p>
        <p class="contact-line"><svg width="7" height="7" viewBox="0 0 10 10"><path d="M2 1l2 2-1 1.5q1.5 2.5 3.5 3.5L8 7l2 2-1.5 1Q3 9 1 2.5z" fill="#1e8bd0"/></svg>1-800-555-0180</p>
        <p class="contact-line"><svg width="7" height="6" viewBox="0 0 10 8"><rect x=".5" y=".5" width="9" height="7" fill="none" stroke="#1e8bd0"/><path d="M.5 .5L5 4.5 9.5.5" fill="none" stroke="#1e8bd0"/></svg>d.ruiz@medora.com</p>
      </div>
      <div class="socials"><span></span><span></span><span></span><span></span><span></span></div>
    </article>
  </div>
</section>

<section class="specialist-group neuro">
  <h2 class="group-heading">Nurology Specialists</h2>
  <div class="card-row">
    <article class="specialist-card">
      <div class="portrait" role="img" aria-label="Portrait of neurologist Nora Quill"></div>
      <div class="card-body"><h3>Nora Quill</h3><p class="role">Senior Neurology Specialist</p>
        <p class="bio">Treating nerve and brain conditions with patient plans and regular online reviews.</p>
        <p class="contact-line"><svg width="7" height="7" viewBox="0 0 10 10"><path d="M2 1l2 2-1 1.5q1.5 2.5 3.5 3.5L8 7l2 2-1.5 1Q3 9 1 2.5z" fill="#1e8bd0"/></svg>1-800-555-0146 · Extension 118</p>
        <p class="contact-line"><svg width="7" height="7" viewBox="0 0 10 10"><path d="M2 1l2 2-1 1.5q1.5 2.5 3.5 3.5L8 7l2 2-1.5 1Q3 9 1 2.5z" fill="#1e8bd0"/></svg>1-800-555-0181</p>
        <p class="contact-line"><svg width="7" height="6" viewBox="0 0 10 8"><rect x=".5" y=".5" width="9" height="7" fill="none" stroke="#1e8bd0"/><path d="M.5 .5L5 4.5 9.5.5" fill="none" stroke="#1e8bd0"/></svg>n.quill@medora.com</p>
      </div>
      <div class="socials"><span></span><span></span><span></span><span></span><span></span></div>
    </article>
    <article class="specialist-card">
      <div class="portrait" role="img" aria-label="Portrait of neurologist Lena Park"></div>
      <div class="card-body"><h3>Lena Park</h3><p class="role">Senior Neurology Specialist</p>
        <p class="bio">Treating nerve and brain conditions with patient plans and regular online reviews.</p>
        <p class="contact-line"><svg width="7" height="7" viewBox="0 0 10 10"><path d="M2 1l2 2-1 1.5q1.5 2.5 3.5 3.5L8 7l2 2-1.5 1Q3 9 1 2.5z" fill="#1e8bd0"/></svg>1-800-555-0147 · Extension 119</p>
        <p class="contact-line"><svg width="7" height="7" viewBox="0 0 10 10"><path d="M2 1l2 2-1 1.5q1.5 2.5 3.5 3.5L8 7l2 2-1.5 1Q3 9 1 2.5z" fill="#1e8bd0"/></svg>1-800-555-0182</p>
        <p class="contact-line"><svg width="7" height="6" viewBox="0 0 10 8"><rect x=".5" y=".5" width="9" height="7" fill="none" stroke="#1e8bd0"/><path d="M.5 .5L5 4.5 9.5.5" fill="none" stroke="#1e8bd0"/></svg>l.park@medora.com</p>
      </div>
      <div class="socials"><span></span><span></span><span></span><span></span><span></span></div>
    </article>
    <article class="specialist-card">
      <div class="portrait" role="img" aria-label="Portrait of neurologist Ian Brooks"></div>
      <div class="card-body"><h3>Ian Brooks</h3><p class="role">Senior Neurology Specialist</p>
        <p class="bio">Treating nerve and brain conditions with patient plans and regular online reviews.</p>
        <p class="contact-line"><svg width="7" height="7" viewBox="0 0 10 10"><path d="M2 1l2 2-1 1.5q1.5 2.5 3.5 3.5L8 7l2 2-1.5 1Q3 9 1 2.5z" fill="#1e8bd0"/></svg>1-800-555-0148 · Extension 120</p>
        <p class="contact-line"><svg width="7" height="7" viewBox="0 0 10 10"><path d="M2 1l2 2-1 1.5q1.5 2.5 3.5 3.5L8 7l2 2-1.5 1Q3 9 1 2.5z" fill="#1e8bd0"/></svg>1-800-555-0183</p>
        <p class="contact-line"><svg width="7" height="6" viewBox="0 0 10 8"><rect x=".5" y=".5" width="9" height="7" fill="none" stroke="#1e8bd0"/><path d="M.5 .5L5 4.5 9.5.5" fill="none" stroke="#1e8bd0"/></svg>i.brooks@medora.com</p>
      </div>
      <div class="socials"><span></span><span></span><span></span><span></span><span></span></div>
    </article>
    <article class="specialist-card">
      <div class="portrait" role="img" aria-label="Portrait of neurologist Maya Ross"></div>
      <div class="card-body"><h3>Maya Ross</h3><p class="role">Senior Neurology Specialist</p>
        <p class="bio">Treating nerve and brain conditions with patient plans and regular online reviews.</p>
        <p class="contact-line"><svg width="7" height="7" viewBox="0 0 10 10"><path d="M2 1l2 2-1 1.5q1.5 2.5 3.5 3.5L8 7l2 2-1.5 1Q3 9 1 2.5z" fill="#1e8bd0"/></svg>1-800-555-0149 · Extension 121</p>
        <p class="contact-line"><svg width="7" height="7" viewBox="0 0 10 10"><path d="M2 1l2 2-1 1.5q1.5 2.5 3.5 3.5L8 7l2 2-1.5 1Q3 9 1 2.5z" fill="#1e8bd0"/></svg>1-800-555-0184</p>
        <p class="contact-line"><svg width="7" height="6" viewBox="0 0 10 8"><rect x=".5" y=".5" width="9" height="7" fill="none" stroke="#1e8bd0"/><path d="M.5 .5L5 4.5 9.5.5" fill="none" stroke="#1e8bd0"/></svg>m.ross@medora.com</p>
      </div>
      <div class="socials"><span></span><span></span><span></span><span></span><span></span></div>
    </article>
  </div>
</section>

<footer class="site-footer">
  <div class="footer-cols">
    <div class="quick-links">
      <h4>QUICK LINKS</h4>
      <ul><li>Home</li><li>Health Packages</li><li>Appointments</li><li>Specialist</li><li>Contact Us</li></ul>
    </div>
    <div class="map" role="img" aria-label="Map showing the clinic location"></div>
    <div class="touch">
      <h4>GET IN TOUCH</h4>
      <p>Reach our care team any day for questions and bookings.</p>
      <div class="row"><svg width="7" height="9" viewBox="0 0 8 10"><path d="M4 0a4 4 0 0 1 4 4c0 3-4 6-4 6S0 7 0 4a4 4 0 0 1 4-4z" fill="#7cc242"/><circle cx="4" cy="4" r="1.4" fill="#0f2a44"/></svg>24 Harbor Way, Suite 5</div>
      <div class="row"><svg width="7" height="7" viewBox="0 0 10 10"><path d="M2 1l2 2-1 1.5q1.5 2.5 3.5 3.5L8 7l2 2-1.5 1Q3 9 1 2.5z" fill="#7cc242"/></svg>Tel: 1-800-555-0100</div>
      <div class="row"><svg width="7" height="6" viewBox="0 0 10 8"><rect x=".5" y=".5" width="9" height="7" fill="none" stroke="#7cc242"/><path d="M.5 .5L5 4.5 9.5.5" fill="none" stroke="#7cc242"/></svg>care@medora.com</div>
    </div>
    <div class="contact-form">
      <h4>CONTACT NOW</h4>
      <div class="form-grid">
        <div class="form-fields"><div class="field">Name</div><div class="field">Email</div><div class="field">Subject</div></div>
        <div class="message">Type Your Message</div>
      </div>
      <div class="submit">Submit</div>
    </div>
  </div>
  <div class="footer-bar">
    <span>© 2015 - Medora. All Rights Reserved</span>
    <div class="footer-social"><span></span><span></span><span></span><span></span></div>
  </div>
  <div class="to-top">top</div>
</footer>
</body>
</html>
```